Template Flyer- Corewell Stretch & Flow

I am wanting a template 1 page flyer designed to use on the back ground of newsletter (faded background) and for our advertising posters in A4, A3, for Facebook and Instagram compatibility.

I have loaded an example from another Studio called Pinegrove (file 3)- each time they have a new workshop to advertise a picture is placed in the little circle (so this is something I would want to do too where I can load a new picture each time a new workshop is running)- They have used the flyer like a water mark...I like this.

Our colour palette is what is on our logos and you can also visit our website for a feel for what we like www.corewellstretch.com.au

I need some of the designs edited a bit more and because of the time difference, there seems to be a 24hour period where we communicate with each other. May I please request another 2 days extension

Requirements
Must have
• Id like to have a picture in the back ground. My favourite back ground that has been produced so far is a background of both picture file 9 and 10 in either.
Nice to have
• 3 picture circles options to advertise the events/workshops I have each year.
• Brush stroke style circles (see picture attached)rather then smooth circles for the picture area (in a grey tone)
Should not have
• No BLACK colour writing or black circles

```html
<!DOCTYPE html>
<html lang="en">
<head>
<meta charset="utf-8">
<title>Corewell Stretch &amp; Flow – Workshop Flyer</title>
<link rel="stylesheet" href="https://fonts.googleapis.com/css2?family=Roboto+Condensed:wght@400;700&family=Roboto:wght@400&display=swap">
<style>
  :root {
    --teal: #1e9bb7;
    --taupe: #b5aa9c;
    --taupe-dark: #9c9082;
    --ink: #3f4346;
    --ink-soft: #55595c;
    --paper: #f2f2f1;
    --stage: #e6e7e8;
    --white: #ffffff;
    --rule: #b9b9b9;
  }
  * { box-sizing: border-box; margin: 0; padding: 0; }
  html, body { width: 768px; height: 1200px; overflow: hidden; }
  body {
    background: var(--stage);
    font-family: "Roboto", Arial, sans-serif;
    position: relative;
  }
  .flyer {
    position: absolute;
    left: 0; top: 57px;
    width: 768px; height: 1086px;
    background: var(--paper);
    overflow: hidden;
    box-shadow: 0 6px 18px rgba(0,0,0,.12);
  }
  .flyer__backdrop {
    position: absolute; inset: 0;
    background:
      radial-gradient(ellipse 260px 180px at 18% 14%, rgba(205,205,203,.75), transparent 70%),
      radial-gradient(ellipse 220px 300px at 88% 22%, rgba(214,214,212,.7), transparent 70%),
      radial-gradient(ellipse 320px 200px at 12% 62%, rgba(210,210,208,.65), transparent 70%),
      radial-gradient(ellipse 300px 220px at 80% 86%, rgba(206,206,204,.7), transparent 70%),
      radial-gradient(ellipse 240px 160px at 40% 96%, rgba(216,216,214,.6), transparent 70%),
      linear-gradient(160deg, #f7f7f6 0%, #e9e9e8 45%, #f3f3f2 70%, #e4e4e3 100%);
    opacity: .9;
  }
  .headline { position: absolute; left: 0; width: 100%; text-align: center; font-family: "Roboto Condensed", "Arial Narrow", sans-serif; }
  .headline__kicker { top: 42px; font-size: 34px; font-weight: 400; color: var(--ink); letter-spacing: -.3px; }
  .headline__title { top: 82px; font-size: 82px; font-weight: 700; color: var(--teal); letter-spacing: -1px; line-height: 1.1; }

  .feature { position: absolute; left: 0; top: 0; }

  .cost-badge {
    position: absolute; left: 76px; top: 474px;
    width: 198px; height: 198px; border-radius: 50%;
    background: var(--taupe);
    border: 5px solid var(--white);
    box-shadow: 0 0 0 3px var(--taupe-dark), 0 4px 10px rgba(0,0,0,.25);
    text-align: center;
    font-family: "Roboto Condensed", "Arial Narrow", sans-serif;
  }
  .cost-badge__label { display: block; margin-top: 34px; font-size: 32px; color: var(--ink); }
  .cost-badge__price { display: block; font-size: 76px; font-weight: 700; color: var(--white); line-height: .95; }

  .detail {
    position: absolute; height: 41px;
    display: flex; align-items: stretch;
    border: 2px solid var(--rule);
    background: var(--white);
    font-family: "Roboto Condensed", "Arial Narrow", sans-serif;
  }
  .detail__label {
    background: var(--teal); color: var(--white);
    font-size: 29px; padding: 0 6px; display: flex; align-items: center;
    margin: -2px 0 -2px -2px;
  }
  .detail__value {
    font-family: "Roboto", Arial, sans-serif;
    font-size: 20px; color: var(--ink); padding: 0 14px; display: flex; align-items: center;
    white-space: nowrap;
  }
  .detail--date { left: 65px; top: 736px; width: 327px; }
  .detail--time { left: 411px; top: 736px; width: 290px; }
  .detail--location { left: 105px; top: 797px; width: 555px; }
  .detail--location .detail__value { letter-spacing: .3px; }

  .workshop { position: absolute; left: 37px; top: 894px; width: 300px; }
  .workshop__title { font-family: "Roboto Condensed", "Arial Narrow", sans-serif; font-size: 30px; font-weight: 400; color: var(--teal); margin-bottom: 6px; }
  .workshop__text { font-size: 10.5px; line-height: 1.35; color: var(--ink-soft); text-align: justify; margin-bottom: 10px; }

  .brand {
    position: absolute; left: 392px; top: 930px;
    display: flex; align-items: center; gap: 10px;
  }
  .brand__mark { width: 40px; height: 40px; border-radius: 50%; border: 3px solid var(--teal); flex: none; }
  .brand__name { font-family: "Roboto", Arial, sans-serif; font-size: 25px; color: var(--teal); white-space: nowrap; }

  .web-band {
    position: absolute; left: 393px; top: 1027px; width: 375px; height: 43px;
    background: var(--teal); border-radius: 22px 0 0 22px;
    color: var(--white); font-size: 23px;
    display: flex; align-items: center; padding-left: 30px;
    white-space: nowrap;
  }
</style>
</head>
<body>
  <main class="flyer">
    <div class="flyer__backdrop" role="img" aria-label="Faded background photo: soft pale grey studio texture washed out behind the flyer content"></div>

    <h2 class="headline headline__kicker">PILATES AND YOGA FOR YOUR</h2>
    <h1 class="headline headline__title">MIND, BODY &amp; SOUL</h1>

    <svg class="feature" width="768" height="1086" viewBox="0 0 768 1086">
      <defs>
        <clipPath id="feature-circle"><circle cx="390" cy="433" r="236"/></clipPath>
        <linearGradient id="studio-tones" x1="0" y1="0" x2="1" y2="1">
          <stop offset="0" stop-color="#e9e8e4"/>
          <stop offset=".45" stop-color="#c9c7c1"/>
          <stop offset=".7" stop-color="#8f9a8c"/>
          <stop offset="1" stop-color="#5d8f96"/>
        </linearGradient>
      </defs>
      <circle class="ring ring--teal" cx="378" cy="447" r="243" fill="var(--teal)"/>
      <circle class="ring ring--taupe" cx="400" cy="423" r="247" fill="var(--taupe)"/>
      <circle cx="390" cy="433" r="238" fill="var(--paper)"/>
      <rect x="150" y="195" width="480" height="480" clip-path="url(#feature-circle)" fill="url(#studio-tones)"
            role="img" aria-label="Workshop photo: studio floor with rows of mats, cork blocks and patterned bolsters"/>
    </svg>

    <div class="cost-badge">
      <span class="cost-badge__label">COST</span>
      <span class="cost-badge__price">$XX</span>
    </div>

    <div class="detail detail--date"><span class="detail__label">DATE</span><span class="detail__value">SUNDAY, XX-XX-2018</span></div>
    <div class="detail detail--time"><span class="detail__label">TIME</span><span class="detail__value">XX am to XX pm</span></div>
    <div class="detail detail--location"><span class="detail__label">LOCATION</span><span class="detail__value">LOREM IPSUM IS SIMPLY DUMMY TEXT</span></div>

    <section class="workshop">
      <h3 class="workshop__title">OUR WORKSHOP</h3>
      <p class="workshop__text">Join us for a gentle morning of mat work and mindful breathing. This workshop blends core strength, balance and stretching so you leave feeling lighter, calmer and ready for the week.</p>
      <p class="workshop__text">All levels are welcome. Mats and props are provided, just bring water and a towel.</p>
    </section>

    <div class="brand">
      <span class="brand__mark"></span>
      <span class="brand__name">Corewell Stretch &amp; Flow</span>
    </div>

    <div class="web-band">www.corewellstretch.com.au</div>
  </main>
</body>
</html>
```